Letterhead for Business Law Firm

We need a letter head for our firm based on the design we have settled on and it is attached. Our clients are small and large businesses around the world, and our letterhead is used typically for formal legal purposes such as demand letters (accusing the recipient of doing bad things) or responding to demand letters. It may also be sent to regulators and other government agencies. So this needs to be tasteful, but a little edgy as well - we try to convey that we are a firm that is different - businesses and investors come to us for creative, quick advice, typically in high stress circumstances, and for our ability to work through high conflict situations, and rapid paced engagements.

Target Market(s)

Lawyers, business executives, investors, government regulators who may receive letters from this firm on behalf of its clients.

Industry/Entity Type

Business

Requirements
Must have
• The design and the firm's contact information:
• Thornwell Law Firm, P.C.
• 1876 NE 57th Ave
• Portland, OR 97213
• phone: 971 555 0147
• fax: 971 555 0182
• in what placement and how depicted (e.g. a phone icon instead of the word "phone") I leave to your creative ideas.
Nice to have
• design and information can be placed at the top, bottom and/or sides of the letter, and the design should be for a standard letter size paper - and can have a separate design for the second page.

```html
<!DOCTYPE html>
<html lang="en">
<head>
<meta charset="utf-8">
<title>Thornwell Law Firm, P.C. — Letterhead</title>
<link href="https://fonts.googleapis.com/css2?family=Source+Sans+3:wght@300;400&display=swap" rel="stylesheet">
<style>
  :root {
    --ink: #231a1c;
    --teal: #4a7a88;
    --text: #3b3b3b;
    --paper: #ffffff;
    --paper-shade: #efefef;
    --ghost: #e4e6e7;
  }
  * { margin: 0; padding: 0; box-sizing: border-box; }
  html, body { width: 933px; height: 1200px; overflow: hidden; background: #ffffff; }
  .letterhead {
    position: relative;
    width: 933px;
    height: 1200px;
    background: linear-gradient(160deg, var(--paper) 25%, var(--paper-shade) 80%);
    font-family: "Source Sans 3", sans-serif;
    color: var(--text);
  }
  .brand {
    position: absolute;
    top: 34px;
    left: 0;
    width: 100%;
    height: 71px;
    display: flex;
    justify-content: center;
    align-items: center;
    gap: 12px;
  }
  .brand-square {
    width: 22px;
    height: 22px;
    background: var(--ink);
  }
  .brand-name {
    font-weight: 300;
    font-size: 40px;
    letter-spacing: 8px;
    color: var(--ink);
    line-height: 1;
  }
  .watermark {
    position: absolute;
    top: 518px;
    left: 0;
    width: 100%;
    height: 163px;
    display: flex;
    justify-content: center;
    align-items: center;
    font-weight: 300;
    font-size: 104px;
    letter-spacing: 14px;
    color: var(--ghost);
    line-height: 1;
  }
  .footer-rule {
    position: absolute;
    top: 1131px;
    height: 4px;
  }
  .footer-rule.accent { left: 0; width: 43px; background: var(--teal); }
  .footer-rule.main { left: 46px; right: 0; background: var(--ink); }
  .contact {
    position: absolute;
    left: 0;
    width: 100%;
    display: flex;
    justify-content: center;
    align-items: center;
    gap: 10px;
    font-weight: 400;
    font-size: 15px;
    line-height: 1;
    white-space: nowrap;
  }
  .contact.line-one { top: 1148px; }
  .contact.line-two { top: 1174px; }
  .contact-item { display: inline-flex; align-items: center; gap: 4px; }
  .contact-label { color: var(--teal); }
  .contact-item svg { width: 13px; height: 13px; fill: none; stroke: var(--teal); stroke-width: 1.6; }
</style>
</head>
<body>
<main class="letterhead">
  <header class="brand">
    <span class="brand-square"></span>
    <span class="brand-name">THORNWELL</span>
  </header>

  <div class="watermark" aria-hidden="true">THORNWELL</div>

  <div class="footer-rule accent"></div>
  <div class="footer-rule main"></div>

  <footer>
    <p class="contact line-one">
      <span class="contact-item" title="Phone">
        <svg viewBox="0 0 16 16" aria-label="Phone"><path d="M4 2l3 3-2 2c1 2 2 3 4 4l2-2 3 3-2 2C7 14 2 9 2 4z"/></svg>
        971 555 0147
      </span>
      <span class="contact-item" title="Fax">
        <svg viewBox="0 0 16 16" aria-label="Fax"><rect x="4" y="1.5" width="8" height="5"/><rect x="1.5" y="6.5" width="13" height="6" rx="1"/><rect x="4" y="10" width="8" height="4.5"/></svg>
        971 555 0182
      </span>
      <span class="contact-item">
        <svg viewBox="0 0 16 16" aria-label="Email"><rect x="1.5" y="4" width="13" height="9" rx="1"/><path d="M1.5 5l6.5 4 6.5-4"/></svg>
        info@thornwelllaw.com
      </span>
      <span class="contact-item">
        <svg viewBox="0 0 16 16" aria-label="Website"><circle cx="8" cy="8" r="6.5"/><ellipse cx="8" cy="8" rx="3" ry="6.5"/><line x1="1.5" y1="8" x2="14.5" y2="8"/></svg>
        www.thornwelllaw.com
      </span>
    </p>
    <p class="contact line-two">
      <span class="contact-item">
        <svg viewBox="0 0 16 16" aria-label="Address"><path d="M1.5 7L8 2.5 14.5 7"/><rect x="3" y="7" width="10" height="7"/><line x1="3" y1="10.5" x2="13" y2="10.5"/></svg>
        Thornwell Law Firm, P.C. · 1876 NE 57th Ave, Portland, OR 97213
      </span>
    </p>
  </footer>
</main>
</body>
</html>
```